TK Stationery - Modern Contemporary

Develop modern template for Letterhead and Stationery (business card, letterhead, envelopes) using the TK Logo and Icon

Colors
0054AA
0677BA
7BADD7
CADEEF
E8F1F8
00AB8E
00BBA5
67D7C9
C6EFE9
E9F9F6
EE7325
F08F49
F5BC92
FAE3D3
FDF4ED
6B429C
8869AF
B7A5CE
E3DAEB
F3F0F8

```html
<!DOCTYPE html>
<html lang="en">
<head>
<meta charset="utf-8">
<title>Tarra Kelo Stationery</title>
<link rel="stylesheet" href="https://fonts.googleapis.com/css2?family=Prata&family=Open+Sans:wght@400;600&family=Crimson+Pro:wght@400&display=swap">
<style>
  :root {
    --navy: #2a2f4c;
    --green: #1db56f;
    --orange: #f08a2c;
    --paper: #ffffff;
    --ink: #3a3d4a;
    --ground: #e3e4e7;
    --sig: #eceef2;
  }
  * { box-sizing: border-box; margin: 0; padding: 0; }
  html, body { width: 941px; height: 1200px; overflow: hidden; }
  body { background: var(--ground); position: relative; font-family: "Open Sans", sans-serif; color: var(--ink); }

  .brand { font-family: "Prata", serif; font-weight: 400; letter-spacing: 0.5px; white-space: nowrap; }
  .contact-serif { font-family: "Crimson Pro", serif; }

  .sheet { position: absolute; background: var(--paper); box-shadow: 0 4px 14px rgba(0,0,0,0.18); overflow: hidden; }

  /* Letterhead */
  .letterhead { left: 40px; top: 40px; width: 440px; height: 570px; }
  .letterhead .band { position: absolute; left: 0; width: 440px; display: block; }
  .letterhead .band-top { top: 0; height: 58px; }
  .letterhead .band-bottom { bottom: 0; height: 24px; }
  .letterhead .brand { position: absolute; left: 40px; top: 11px; font-size: 21px; color: var(--paper); }
  .header-contacts { position: absolute; left: 300px; top: 9px; list-style: none; color: var(--paper); font-size: 8.8px; line-height: 12px; }
  .header-contacts li { display: flex; align-items: center; gap: 4px; }
  .dot-icon { width: 9px; height: 9px; flex: none; }
  .letter-body { position: absolute; left: 41px; top: 108px; width: 356px; font-size: 6.6px; line-height: 12.5px; }
  .letter-body .meta { line-height: 8.4px; margin-bottom: 24px; }
  .letter-body .date { margin-bottom: 9px; line-height: 8.4px; }
  .letter-body .greeting { margin-bottom: 13px; }
  .letter-body p.para { margin-bottom: 12.5px; text-align: justify; }
  .letter-body .closing { margin-top: 25px; }
  .signature-area { width: 100px; height: 14px; background: var(--sig); margin: 6px 0 5px; }
  .signer-name { font-size: 8.6px; font-weight: 600; color: var(--ink); line-height: 11px; }
  .signer-title { font-size: 6.6px; line-height: 11px; }
  .footer-address { position: absolute; left: 31px; bottom: 5px; display: flex; align-items: center; gap: 6px; color: var(--paper); font-size: 8.6px; }

  /* Envelopes */
  .envelope-front { left: 520px; top: 210px; width: 380px; height: 190px; }
  .envelope-front .brand { position: absolute; left: 26px; top: 18px; font-size: 20px; color: var(--navy); }
  .envelope-front .band { position: absolute; left: 0; bottom: 0; width: 380px; height: 22px; display: block; }
  .envelope-front .address { position: absolute; left: 22px; bottom: 6px; font-size: 6.6px; color: var(--paper); }

  .envelope-back { left: 522px; top: 428px; width: 378px; height: 188px; }
  .envelope-back .flap { position: absolute; left: 0; top: 0; width: 378px; height: 44px; display: block; }
  .envelope-back .brand { position: absolute; left: 0; right: 0; top: 9px; text-align: center; font-size: 18px; color: var(--paper); }

  /* Business cards */
  .card { width: 400px; height: 228px; top: 700px; border-bottom: 3px solid var(--green); }
  .card-front { left: 40px; }
  .card-front .brand { position: absolute; left: 34px; top: 98px; font-size: 24px; color: var(--navy); }
  .card-front .divider { position: absolute; left: 205px; top: 58px; width: 1px; height: 112px; background: #d8dae0; }
  .card-details { position: absolute; left: 222px; top: 62px; }
  .card-name { font-family: "Prata", serif; font-size: 14px; color: var(--navy); line-height: 17px; }
  .card-role { font-size: 8px; color: var(--ink); margin-bottom: 10px; }
  .card-contacts { list-style: none; font-size: 8px; line-height: 13px; color: var(--ink); }
  .card-contacts li { display: flex; align-items: flex-start; gap: 5px; }
  .card-contacts .dot-icon { margin-top: 2px; }

  .card-back { left: 501px; background: var(--navy); }
  .card-back .tone { position: absolute; inset: 0; background: linear-gradient(135deg, #2d3352, #262a45); }
  .card-back .brand { position: absolute; right: 28px; bottom: 30px; font-size: 24px; color: var(--paper); }
</style>
</head>
<body>

<svg width="0" height="0" style="position:absolute">
  <defs>
    <symbol id="icon-phone" viewBox="0 0 10 10"><circle cx="5" cy="5" r="5" fill="#f08a2c"/><path d="M3.2 2.6c.3-.3.7-.3.9 0l.5.7c.2.3.1.6-.1.8l-.3.3c.3.7.8 1.2 1.5 1.5l.3-.3c.2-.2.5-.3.8-.1l.7.5c.3.2.3.6 0 .9-.6.6-1.4.7-2.2.2-1.1-.7-2-1.6-2.6-2.7-.4-.7-.3-1.3.5-1.8z" fill="#fff"/></symbol>
    <symbol id="icon-mail" viewBox="0 0 10 10"><circle cx="5" cy="5" r="5" fill="#f08a2c"/><rect x="2.6" y="3.3" width="4.8" height="3.4" fill="#fff"/><path d="M2.6 3.3 5 5.2 7.4 3.3" stroke="#f08a2c" stroke-width=".6" fill="none"/></symbol>
    <symbol id="icon-web" viewBox="0 0 10 10"><circle cx="5" cy="5" r="5" fill="#f08a2c"/><circle cx="5" cy="5" r="2.5" fill="none" stroke="#fff" stroke-width=".7"/><path d="M2.5 5h5M5 2.5c-1.2 1.4-1.2 3.6 0 5M5 2.5c1.2 1.4 1.2 3.6 0 5" stroke="#fff" stroke-width=".5" fill="none"/></symbol>
    <symbol id="icon-pin" viewBox="0 0 10 10"><circle cx="5" cy="5" r="5" fill="#f08a2c"/><path d="M5 2.2a2 2 0 0 0-2 2c0 1.5 2 3.6 2 3.6s2-2.1 2-3.6a2 2 0 0 0-2-2z" fill="#fff"/><circle cx="5" cy="4.2" r=".8" fill="#f08a2c"/></symbol>
  </defs>
</svg>

<!-- Letterhead -->
<section class="sheet letterhead" aria-label="Letterhead">
  <svg class="band band-top" viewBox="0 0 440 58" preserveAspectRatio="none">
    <polygon points="0,0 440,0 440,57 280,57 270,47 0,47" fill="var(--navy)"/>
    <polygon points="0,46.5 268,46.5 273,52 0,52" fill="var(--paper)"/>
    <polygon points="0,48.5 266,48.5 271,53 0,53" fill="var(--green)"/>
  </svg>
  <div class="brand">tarra kelo</div>
  <ul class="header-contacts contact-serif">
    <li><svg class="dot-icon"><use href="#icon-phone"/></svg>021-555 0147</li>
    <li><svg class="dot-icon"><use href="#icon-mail"/></svg>hello@tarrakelo.com</li>
    <li><svg class="dot-icon"><use href="#icon-web"/></svg>www.tarrakelo.com</li>
  </ul>

  <div class="letter-body">
    <p class="date">Issuing Date: May 5, 2018</p>
    <p class="meta">Name Of Employee Mr. XYZABC<br>Address of Employee<br>Address Line 2 etc..</p>
    <p class="greeting">Dear Mr.XYZABC</p>
    <p class="para">Lorem Ipsum has been the industry's standard dummy text ever since the 1500s, when an unknown printer took a galley of type and scrambled it to make a type specimen book. It has survived not only five centuries, but also the leap into electronic typesetting, remaining essentially unchanged. It was popularised in the 1960s with the release of Letraset sheets containing Lorem Ipsum passages, and more recently with desktop publishing software like Aldus PageMaker including versions of Lorem Ipsum.</p>
    <p class="para">Lorem Ipsum is simply dummy text of the printing and typesetting industry. Lorem Ipsum has been the industry's standard dummy text ever since the 1500s, when an unknown printer took a galley of type and scrambled it to make a type specimen book.</p>
    <p class="para">It has survived not only five centuries, but also the leap into electronic typesetting, remaining essentially unchanged. It was popularised in the 1960s with the release of Letraset sheets containing Lorem Ipsum passages.</p>
    <p class="closing">Yours Sincerely</p>
    <div class="signature-area" role="img" aria-label="Handwritten signature"></div>
    <p class="signer-name">Elias Marren</p>
    <p class="signer-title">Managing Director</p>
  </div>

  <svg class="band band-bottom" viewBox="0 0 440 24" preserveAspectRatio="none">
    <polygon points="0,0 258,0 270,12 440,12 440,24 0,24" fill="var(--navy)"/>
    <polygon points="272,6 440,6 440,11 276,11" fill="var(--green)"/>
  </svg>
  <div class="footer-address contact-serif"><svg class="dot-icon"><use href="#icon-pin"/></svg>18 Linden Row, Harbour City, 40219</div>
</section>

<!-- Envelope front -->
<section class="sheet envelope-front" aria-label="Envelope front">
  <div class="brand">tarra kelo</div>
  <svg class="band" viewBox="0 0 380 22" preserveAspectRatio="none">
    <polygon points="0,4 208,4 222,22 0,22" fill="var(--navy)"/>
    <polygon points="224,10 380,10 380,15 228,15" fill="var(--green)"/>
    <polygon points="228,17 380,17 380,22 232,22" fill="var(--navy)"/>
  </svg>
  <div class="address contact-serif">18 Linden Row, Harbour City, 40219</div>
</section>

<!-- Envelope back -->
<section class="sheet envelope-back" aria-label="Envelope back">
  <svg class="flap" viewBox="0 0 378 44" preserveAspectRatio="none">
    <polygon points="0,0 378,0 364,44 14,44" fill="var(--navy)"/>
  </svg>
  <div class="brand">tarra kelo</div>
</section>

<!-- Business card front -->
<section class="sheet card card-front" aria-label="Business card front">
  <div class="brand">tarra kelo</div>
  <div class="divider"></div>
  <div class="card-details">
    <p class="card-name">Elias Marren</p>
    <p class="card-role">Managing Director</p>
    <ul class="card-contacts">
      <li><svg class="dot-icon"><use href="#icon-phone"/></svg>021-555 0147</li>
      <li><svg class="dot-icon"><use href="#icon-mail"/></svg>hello@tarrakelo.com</li>
      <li><svg class="dot-icon"><use href="#icon-web"/></svg>www.tarrakelo.com</li>
      <li><svg class="dot-icon"><use href="#icon-pin"/></svg>18 Linden Row,<br>Harbour City, 40219</li>
    </ul>
  </div>
</section>

<!-- Business card back -->
<section class="sheet card card-back" aria-label="Business card back">
  <div class="tone" role="img" aria-label="Tonal repeated wordmark pattern on navy"></div>
  <div class="brand">tarra kelo</div>
</section>

</body>
</html>
```